Give Gold Kite an Online Presence!

Gold Kite Property Maintenance is an Australian Owned property maintenance company who needs a stand out online presence.

GK maintains many buildings and sites and wants to appeal to a corporate professional market with their brand new website. GK is essentially a handyman service offering all maintenance services to home owners, office managers, real estate agents and strata managers.

The Website:
We need a corporate website that appeals to our broader customer base (property owners, property managers, office managers) the copy is being written by a professional so use filler text for now.

Things that we want:
Home page that sets us apart and appeals to the corporate and residential market. The home page needs to not focus on either the residential or commercial market. The home page should focus on our logo and branding. We have a logo already and it is attached to the brief, please use it and try to consider the colour pallette that goes with it. Whilst we want the site to appear strong and manly it is important to remember that 95% of our customers are female so we need the site to be appealing to women. Women need to believe that we are strong, dependable and trustworthy.
We'd like a quote page and potentially also the ability to get a quote from the home page (please don't put it in if it ruins the overall feel of the home page)
An "about us" page
A contact us page
A blog that's built in (we don't want to link to an external blog)
(overall we'd expect to have 6 or 7 pages total)

The site will also need coding - we expect this to be done in a separate project but need you to consider a few things about the coding side of things.

It needs to be iPhone and iPad compatible.

We'd like you to suggest the best CMS that you would use or if you would suggest not using a CMS please let us know with your submissions.

Target Market(s)

Property owners, office managers and property managers who need maintenance on buildings (So all of them)

Industry/Entity Type

Property Maintenance

Requirements
Must have
• Our Logo
Home page
About Us
Residential
Commercial
Real Estate/Strata
Contact Us/Quote
Blog
Nice to have
• Quote form included in home page
Movement on the home page at least
Should not have
• other logos, too much colour
NO FLASH

```html
<!DOCTYPE html>
<html lang="en">
<head>
<meta charset="utf-8">
<title>Gold Kite Property Maintenance – Housing Maintenance</title>
<link rel="stylesheet" href="https://fonts.googleapis.com/css2?family=PT+Sans:wght@400;700&family=PT+Sans+Narrow:wght@400;700&display=swap">
<style>
  :root{
    --orange:#f47a12;
    --orange-light:#fb8f2a;
    --orange-dark:#e2670a;
    --ink:#2a2a2a;
    --text:#3c3c3c;
    --muted:#777;
    --line:#dcdcdc;
    --top-rule:#c9c9c4;
    --footer-bg:#efefef;
    --white:#fff;
    --btn:#111;
  }
  *{box-sizing:border-box;margin:0;padding:0}
  html,body{width:1098px;height:1200px;overflow:hidden;background:var(--white)}
  body{position:relative;font-family:"PT Sans",Arial,sans-serif;color:var(--text)}
  .top-rule{position:absolute;left:0;top:0;width:1098px;height:5px;background:var(--top-rule)}

  /* Header */
  .brand{position:absolute;left:47px;top:40px;display:flex;align-items:center;gap:10px}
  .brand-mark{width:26px;height:26px;background:var(--orange);border-radius:3px}
  .brand-name{font-family:"PT Sans Narrow",Arial,sans-serif;font-weight:700;font-size:22px;line-height:1.05;color:var(--orange);text-transform:uppercase;width:150px}
  .call{position:absolute;left:761px;top:50px;font-size:21px;color:var(--ink);letter-spacing:.2px}
  .call strong{font-weight:400;color:#111}
  .social{position:absolute;top:49px;width:30px;height:30px;border-radius:50%;background:#111}
  .social.one{left:996px}
  .social.two{left:1027px}
  .search{position:absolute;left:775px;top:94px;width:289px;height:35px;border:1px solid var(--line);background:var(--white);box-shadow:inset 0 1px 2px rgba(0,0,0,.06)}
  .search span{position:absolute;left:11px;top:8px;font-size:13px;color:#888}
  .search svg{position:absolute;right:9px;top:8px}

  /* Nav */
  .nav{position:absolute;left:30px;top:149px;width:1038px;height:53px;border-radius:4px;background:linear-gradient(var(--orange-light),var(--orange) 55%,var(--orange-dark));display:flex}
  .nav a{display:flex;align-items:center;justify-content:center;color:var(--white);text-decoration:none;font-size:16px;letter-spacing:.3px;text-transform:uppercase;border-right:1px solid rgba(255,255,255,.28);box-shadow:1px 0 0 rgba(180,70,0,.25)}
  .nav a:last-child{border-right:0;box-shadow:none}

  /* Hero */
  .hero{position:absolute;left:31px;top:212px;width:1034px;height:421px;border:1px solid #e3e3e3;border-radius:4px;background:var(--white)}
  .hero-shadow{position:absolute;left:60px;top:632px;width:980px;height:22px;background:radial-gradient(ellipse at top,rgba(0,0,0,.16),rgba(0,0,0,0) 70%)}
  .hero-photo{position:absolute;left:28px;top:212px;width:574px;height:421px;background:linear-gradient(160deg,#e9d3b8 0%,#d7a77a 35%,#2d6db8 65%,#f1ece2 100%);border-radius:3px 0 0 3px}
  .hero-copy{position:absolute;left:644px;top:266px;width:380px}
  .hero-kicker{font-family:"PT Sans Narrow",Arial,sans-serif;font-weight:700;font-size:27px;color:var(--ink);text-transform:uppercase;line-height:1.1}
  .hero-title{font-family:"PT Sans Narrow",Arial,sans-serif;font-weight:700;font-size:33px;color:var(--orange);text-transform:uppercase;line-height:1.15;margin-top:2px}
  .hero-lead{font-family:"PT Sans Narrow",Arial,sans-serif;font-size:15.5px;line-height:21px;color:var(--ink);margin-top:6px}
  .hero-list{list-style:none;margin-top:18px}
  .hero-list li{font-family:"PT Sans Narrow",Arial,sans-serif;font-size:15.5px;color:var(--ink);height:32px;display:flex;align-items:center;gap:10px}

  /* Welcome */
  .welcome{position:absolute;left:47px;top:674px;width:647px}
  .welcome h1{font-family:"PT Sans Narrow",Arial,sans-serif;font-weight:700;font-size:23px;color:#111;text-transform:uppercase}
  .welcome .intro{font-weight:700;font-size:13.5px;line-height:21px;color:var(--orange);margin-top:8px}
  .welcome p.body{font-size:13px;line-height:21.5px;text-align:justify;color:var(--text);margin-top:12px}
  .welcome-list{list-style:none;margin-top:14px}
  .welcome-list li{font-weight:700;font-size:12.5px;color:var(--orange);height:32px;display:flex;align-items:center;gap:8px}

  /* Contact form */
  .form-card{position:absolute;left:722px;top:672px;width:335px;height:442px;border:1px solid #e0e0e0;border-radius:4px;background:var(--white)}
  .form-head{height:49px;background:var(--orange);border-radius:4px 4px 0 0;padding:12px 0 0 24px;font-family:"PT Sans Narrow",Arial,sans-serif;font-weight:700;font-size:22px;color:var(--white)}
  .form-body{padding:14px 18px 0 18px}
  .field label{display:block;font-size:13px;color:#222;margin-bottom:5px}
  .field .input{height:30px;border:1px solid var(--line);margin-bottom:14px}
  .field .area{height:100px;border:1px solid var(--line);margin-bottom:12px}
  .submit{display:inline-block;width:91px;height:34px;border-radius:4px;background:linear-gradient(#3a3a3a,var(--btn) 50%);color:var(--white);font-size:14px;text-align:center;line-height:34px;text-transform:uppercase}

  /* Footer */
  .footer{position:absolute;left:0;top:1145px;width:1098px;height:55px;background:var(--footer-bg)}
  .footer p{position:absolute;left:53px;top:19px;font-size:11px;color:#444}
</style>
</head>
<body>
  <div class="top-rule"></div>

  <header>
    <div class="brand">
      <span class="brand-mark"></span>
      <span class="brand-name">Gold Kite Property Maintenance</span>
    </div>
    <div class="call">CALL US <strong>+685 555 0142</strong></div>
    <span class="social one"></span>
    <span class="social two"></span>
    <div class="search">
      <span>enter keyword</span>
      <svg width="19" height="19" viewBox="0 0 19 19"><circle cx="8" cy="8" r="6" fill="none" stroke="#777" stroke-width="2.6"/><line x1="12.5" y1="12.5" x2="17.5" y2="17.5" stroke="#777" stroke-width="3" stroke-linecap="round"/></svg>
    </div>
  </header>

  <nav class="nav">
    <a style="width:114px">Home</a>
    <a style="width:128px">About Us</a>
    <a style="width:150px">Residential</a>
    <a style="width:157px">Commercial</a>
    <a style="width:219px">Real Estate/Strata</a>
    <a style="width:148px">Contact Us</a>
    <a style="width:122px">Blog</a>
  </nav>

  <section>
    <div class="hero"></div>
    <div class="hero-shadow"></div>
    <div class="hero-photo" role="img" aria-label="Smiling painter in a cap holding paint rollers and brushes, giving a thumbs up"></div>
    <div class="hero-copy">
      <div class="hero-kicker">Gold Kite puch line goes here</div>
      <div class="hero-title">Housing Maintenance</div>
      <p class="hero-lead">Class aptent taciti sociosqu ad litora torquent per conubia nostra, per inceptos hymenaeos. Proin nulla arcu, nonummy luctus, dictum eget, fermentum et, lorem.</p>
      <ul class="hero-list">
        <li><svg width="14" height="12" viewBox="0 0 14 12"><path d="M1 6.5l4 4L13 1.5" fill="none" stroke="#222" stroke-width="2.6"/></svg>Curabitur tristique mi condimentum orci.</li>
        <li><svg width="14" height="12" viewBox="0 0 14 12"><path d="M1 6.5l4 4L13 1.5" fill="none" stroke="#222" stroke-width="2.6"/></svg>Phasellus pellentesque aliquam enim.</li>
        <li><svg width="14" height="12" viewBox="0 0 14 12"><path d="M1 6.5l4 4L13 1.5" fill="none" stroke="#222" stroke-width="2.6"/></svg>Proin dui lectus, cursus eu, mattis laoreet.</li>
        <li><svg width="14" height="12" viewBox="0 0 14 12"><path d="M1 6.5l4 4L13 1.5" fill="none" stroke="#222" stroke-width="2.6"/></svg>Ut velit enim, vestibulum non.</li>
      </ul>
    </div>
  </section>

  <main class="welcome">
    <h1>Welcome to our website landing page</h1>
    <p class="intro">Pellentesque habitant morbi tristique senectus et netus et malesuada fames ac turpis egestas. In posuere felis nec tortor. Pellentesque faucibus.</p>
    <p class="body">Ut accumsan ultricies elit. Maecenas at justo id velit placerat molestie. Donec dictum lectus non odio. Cras a ante vitae enim iaculis aliquam. Mauris nunc quam, venenatis nec, euismod sit amet, egestas placerat, est. Pellentesque habitant morbi tristique senectus et netus et malesuada fames ac turpis egestas. Cras id elit. Integer quis urna. Ut ante enim, dapibus malesuada, fringilla eu, condimentum quis, tellus. Aenean porttitor eros vel dolor. Donec convallis pede venenatis nibh. Duis quam. Nam eget lacus. Aliquam erat volutpat. Quisque dignissim congue leo.</p>
    <p class="body">Mauris vel lacus vitae felis vestibulum volutpat. Etiam est nunc, venenatis in, tristique eu, imperdiet ac, nisl. Cum sociis natoque penatibus et magnis dis parturient montes, nascetur ridiculus mus. In iaculis facilisis massa. Etiam eu urna. Sed porta. Suspendisse quam leo, molestie sed, luctus quis, feugiat in, pede. Fusce tellus. Sed metus augue, convallis et, vehicula ut, pulvinar eu, ante. Integer orci tellus.</p>
    <ul class="welcome-list">
      <li><svg width="14" height="12" viewBox="0 0 14 12"><path d="M1 6.5l4 4L13 1.5" fill="none" stroke="#f47a12" stroke-width="2.6"/></svg>Pellentesque nibh libero, ultricies eu, sagittis non, mollis sed, justo.</li>
      <li><svg width="14" height="12" viewBox="0 0 14 12"><path d="M1 6.5l4 4L13 1.5" fill="none" stroke="#f47a12" stroke-width="2.6"/></svg>Praesent metus ipsum, pulvinar pulvinar, porta id.</li>
      <li><svg width="14" height="12" viewBox="0 0 14 12"><path d="M1 6.5l4 4L13 1.5" fill="none" stroke="#f47a12" stroke-width="2.6"/></svg>Curabitur vel mi sit amet magna malesuada ultrices ut nisi erat, fermentum vel.</li>
    </ul>
  </main>

  <aside class="form-card">
    <div class="form-head">Fill Our Contact Form</div>
    <div class="form-body">
      <div class="field"><label>Full Name</label><div class="input"></div></div>
      <div class="field"><label>Email address</label><div class="input"></div></div>
      <div class="field"><label>Phone no.</label><div class="input"></div></div>
      <div class="field"><label>Message</label><div class="area"></div></div>
      <span class="submit">Submit</span>
    </div>
  </aside>

  <footer class="footer">
    <p>© 2012 Company Name.&nbsp; All right reserved. Term of Use</p>
  </footer>
</body>
</html>
```